we can communicate on this, but i want to follow the approach we took on Pellew|Marsh & Quinlan but i feel the card front needs the black background and the platinum and gold logo. The back? I am open. we can use the same info from PM&Q. Velmont Arc is an enhanced equity investment fund - basically a very exclusive boutique hedge fund that uses only stock options. very advanced things. hope you are interested

Contact Information for Business Card

Dr. Lewis T. Brennick, CFA
Scientifique de fusée financière
701.555.0143
LTBquant47@mailvantor.com

4718 Willow Creek Bend W.
West Fargo, ND 58078

No web site

Colors

Designer to choose colors to be used in the design.

Requirements
Nice to have
• I tend to prefer the most visible applications of the logo to include logo and name, the logo version with a black background and the gold and platinum components separated by the black. I see this working well for a single side (logo and name - this is card front to me).
• I am fairly open to other treatments on the reverse side with the data. To me, it makes sense to have a different color rendition of the logo on the reverse and it may be a muted black tone on tone or an oversized portion that would have spot UV. Or, the reverse may play with colors and layout
Should not have
• Other colors = no no
• Decorative font

```html
<!DOCTYPE html>
<html lang="en">
<head>
<meta charset="utf-8">
<title>Velmont Arc — Business Card</title>
<link rel="stylesheet" href="https://fonts.googleapis.com/css2?family=Montserrat:wght@700&family=Roboto:wght@400;700&display=swap">
<style>
  :root {
    --backdrop: #1b1b1c;
    --card: #141414;
    --card-edge: #0c0c0c;
    --pattern-light: #26262a;
    --pattern-dark: #151516;
    --gold: #d9b23c;
    --gold-deep: #b8902a;
    --white: #f4f4f4;
  }
  html, body {
    margin: 0;
    width: 1200px;
    height: 800px;
    overflow: hidden;
    background: var(--backdrop);
  }
  .stage {
    position: relative;
    width: 1200px;
    height: 800px;
  }
  .card {
    position: absolute;
    width: 500px;
    height: 286px;
    background: var(--card);
    box-shadow: 0 18px 40px rgba(0,0,0,0.55), 0 0 0 1px var(--card-edge);
    overflow: hidden;
  }
  /* Pattern side */
  .card--pattern {
    left: 250px;
    top: 105px;
  }
  .pattern-field {
    position: absolute;
    inset: 0;
    background: radial-gradient(ellipse at 25% 70%, var(--pattern-light) 0%, var(--pattern-dark) 70%);
  }
  .corner-mark {
    position: absolute;
    right: 34px;
    bottom: 40px;
    display: flex;
    align-items: center;
    gap: 8px;
    font-family: "Montserrat", sans-serif;
    font-weight: 700;
    font-size: 15px;
    letter-spacing: 1px;
    text-transform: uppercase;
    color: var(--gold);
  }
  .corner-mark .dot {
    width: 14px;
    height: 14px;
    border-radius: 50%;
    background: var(--gold);
  }
  /* Info side */
  .card--info {
    left: 450px;
    top: 409px;
  }
  .brand {
    position: absolute;
    left: 40px;
    top: 36px;
    display: flex;
    flex-direction: column;
    align-items: flex-start;
    gap: 12px;
  }
  .brand .disc {
    width: 62px;
    height: 62px;
    border-radius: 50%;
    background: linear-gradient(135deg, var(--gold) 0%, var(--gold-deep) 100%);
  }
  .brand .wordmark {
    font-family: "Montserrat", sans-serif;
    font-weight: 700;
    font-size: 25px;
    letter-spacing: 1px;
    text-transform: uppercase;
    color: var(--white);
  }
  .person {
    position: absolute;
    left: 40px;
    bottom: 38px;
    font-family: "Roboto", sans-serif;
  }
  .person .name {
    margin: 0;
    font-weight: 700;
    font-size: 17px;
    color: var(--gold);
  }
  .person .name .credential {
    font-size: 10px;
    vertical-align: 5px;
  }
  .person .role {
    margin: 3px 0 0;
    font-weight: 400;
    font-size: 10.5px;
    color: var(--white);
  }
  .contact {
    position: absolute;
    right: 30px;
    top: 128px;
    font-family: "Roboto", sans-serif;
    font-size: 10.5px;
    line-height: 1.35;
    color: var(--white);
  }
  .contact address {
    font-style: normal;
    margin: 0 0 10px;
  }
  .contact ul {
    list-style: none;
    margin: 0;
    padding: 0;
  }
  .contact li {
    display: flex;
    align-items: center;
    gap: 7px;
  }
  .contact svg {
    width: 10px;
    height: 10px;
    flex: none;
  }
</style>
</head>
<body>
<main class="stage">

  <section class="card card--pattern" aria-label="Card back">
    <div class="pattern-field" role="img" aria-label="Tone-on-tone repeating brand mark pattern in spot UV"></div>
    <div class="corner-mark"><span class="dot"></span>Velmont Arc</div>
  </section>

  <section class="card card--info" aria-label="Card front">
    <div class="brand">
      <span class="disc"></span>
      <span class="wordmark">Velmont Arc</span>
    </div>

    <div class="person">
      <p class="name">Dr. Lewis T. Brennick, <span class="credential">CFA</span></p>
      <p class="role">Scientifique de fusée financière</p>
    </div>

    <div class="contact">
      <address>4718 Willow Creek Bend W.<br>West Fargo, ND 58078</address>
      <ul>
        <li>
          <svg viewBox="0 0 10 10" aria-hidden="true"><rect x="2.5" y="0.5" width="5" height="9" rx="1" fill="none" stroke="#d9b23c" stroke-width="1"/><rect x="4" y="7.5" width="2" height="0.8" fill="#d9b23c"/></svg>
          701.555.0143
        </li>
        <li>
          <svg viewBox="0 0 10 10" aria-hidden="true"><rect x="0.5" y="2" width="9" height="6.5" fill="#d9b23c"/><polyline points="0.5,2 5,5.8 9.5,2" fill="none" stroke="#141414" stroke-width="1"/></svg>
          LTBquant47@mailvantor.com
        </li>
      </ul>
    </div>
  </section>

</main>
</body>
</html>
```